Creative UI design for web application

I need a new UI design for my web application. It will be used by small and micro business owners to plan & implement growth tactics.

I've attached the current design (which I'm open to be changed) - but in particular I need to design the centre of the screen, where the work actually happens.

There needs to be place for a title (YOUR BUSINESS) and description (say 1-2 paragraphs of text) - and am happy to include icons or imagery where makes sense. It may make sense for the user to be able to upload their business logo and name, for example.

This screen will be used by the business owner to understand the real value they offer potential customers and their point of difference - why they exist and why potential customers should care.

They'll use the information they put into this screen to plan things like their messaging.

Following that, there needs to be 2 sections in the dashboard.

The first section is titled "WHO YOU ARE"

The first section will include a number of boxes that the user can input information into, as follows:

- Logo
- Business name
- Business tag line
- Business vision
- Business bio
- Brand colours (these should end up as swatches based on the colour code they enter) - the colour code for each colour swatch should also be visible.
- Key competitors
- SWOT analysis (boxes to enter their strengths, weaknesses, opportunities and threats).

The second section is titled "WHY YOU EXIST"

The second section will include a number of boxes that the user can input information (text) into, as follows:

- Who are your ideal customers?
- What problem are you trying to solve for them?
- What pain points will this remove for them?
- How do you solve it?
- How else could this problem be solved?
- Who offers these other solutions?
- Why is your solution better?
- How much does your solution cost?
- What value are you providing to justify this cost?
- How will this make their life/job easier/better?

They should be able to write a decent amount of information in the boxes.

There should ideally be a place for a description for each of these text fields (for both section 1 & 2) as well so I can give them a little bit more direction around what to put in the box. Alternatively there could be a little icon (say a question mark or "i") that they could click on to view instructions. The instructions will be around 2-4 sentences long for each text field.

You have 2 options:

a) This all needs to appear on the one screen, and the navigation needs to be visible (as per the example attached but feel free to recreate this navigation)

Note: the page can scroll below the fold - but please provide the design for the full length of the page.

b) Potentially the 2 sections could actually be in 2 different items in the menu - YOUR BUSINESS and YOUR VALUE (which would sit next to YOUR BUSINESS and before YOUR CUSTOMER in the screenshot provided). feel free to design them as 2 separate screens if you prefer.

I have attached a screenshot of the app as it stands today (screen shot 2017) which would still exist in the new design but under a different section (the learn section from the plan2 mockup attached)

I have mocked up how this new screen could look if broken into 2 and that's also attached. If you can make this come to life - and look more engaging that would be helpful! :)

Target Market(s)

Small and micro business owners

Industry/Entity Type

Marketing

Number of Pages Required

1 page

Font styles to use
Sans Serif
Other font styles liked:
• Montserrat

Colors
87cfc6
d2a4cc
ffffff
85cae6
e8e8e8
5c5c5c

Requirements
Must have
• Use of my brand colours: #cc8eb2, #76d6c8, #68c7ff as well as white and #595959. Must be visually pleasing / engaging, designed for desktop (as it's a desktop application), really easy to use / navigate.
• Use font Montserrat light & Montserrat Regular or Bold. Mostly should be Montserrat light.
Nice to have
• Would be nice to see how this would look on mobile (as the application is responsive) but this is not mandatory.
Should not have
• Should not look too corporate or dry.

```html
<!DOCTYPE html>
<html lang="en">
<head>
<meta charset="utf-8">
<title>Bloomwise – Your Business</title>
<link href="https://fonts.googleapis.com/css2?family=Montserrat:wght@300;400;500;600&display=swap" rel="stylesheet">
<style>
:root{
  --pink:#d2a4cc;
  --pink-dark:#cc8eb2;
  --teal:#87cfc6;
  --ink:#5c5c5c;
  --ink-dark:#333333;
  --bar:#3b3b3b;
  --subbar:#6a6a6a;
  --page:#f0f0f0;
  --line:#d6d6d6;
  --white:#ffffff;
  --icon:#b8b8b8;
}
*{box-sizing:border-box;margin:0;padding:0}
html,body{width:1200px;height:2703px;overflow:hidden}
body{font-family:'Montserrat',sans-serif;font-weight:300;color:var(--ink);background:var(--page);position:relative}
.topbar{position:absolute;left:0;top:0;width:1200px;height:49px;background:var(--bar);color:var(--white)}
.brand{position:absolute;font-weight:500;font-size:19px;letter-spacing:.5px;color:var(--white)}
.topbar .brand{left:130px;top:14px}
.mainnav a,.usernav a{position:absolute;top:18px;font-size:12px;font-weight:400;color:var(--white);text-decoration:none}
.subbar{position:absolute;left:0;top:49px;width:1200px;height:41px;background:linear-gradient(#727272,#616161)}
.subbar a{position:absolute;top:0;height:41px;line-height:41px;font-size:12px;font-weight:400;color:var(--white);text-decoration:none}
.subbar a.active{background:var(--pink);padding:0 15px}
.hero{position:absolute;left:0;top:90px;width:1200px;height:443px;background:var(--white)}
.profile-card{position:absolute;left:132px;top:47px;width:935px;height:353px;border:1px solid var(--line)}
.profile-mark{position:absolute;left:38px;top:33px;width:86px;height:86px;border-radius:50%;background:#111}
.profile-name{position:absolute;left:176px;top:32px;font-size:21px;font-weight:400;color:var(--ink-dark)}
.profile-email{position:absolute;left:176px;top:64px;font-size:13px;font-weight:400;color:var(--ink-dark)}
.profile-bio{position:absolute;left:176px;top:94px;width:337px;font-size:11px;line-height:21.6px;text-align:justify;color:var(--ink-dark)}
.profile-bio p+p{margin-top:17px}
.profile-photo{position:absolute;left:548px;top:32px;width:358px;height:287px;background:linear-gradient(135deg,#e8cfc8,#c9a5a2 55%,#8a6d6e)}
.section-title{position:absolute;left:130px;font-size:22px;font-weight:500;color:var(--pink);letter-spacing:.5px}
.panel{position:absolute;left:132px;width:935px;background:var(--white);border:1px solid var(--line)}
.field{position:absolute;width:423px;border:1px solid var(--line);background:var(--white)}
.field .label{position:absolute;left:14px;top:11px;font-size:11px;font-weight:400;color:var(--ink)}
.info{position:absolute;right:12px;top:10px;width:14px;height:14px}
.field.short{height:36px}
.field.tall{height:133px}
.upload{position:absolute;right:0;top:0;width:88px;height:34px;background:var(--teal);color:#2f5f59;font-size:10px;font-weight:500;line-height:34px;text-align:center}
.upload svg{vertical-align:-2px;margin-right:5px}
.field.with-upload .info{right:100px}
.small-label{position:absolute;left:33px;font-size:11px;font-weight:400;color:var(--ink-dark)}
.swatches{position:absolute;left:126px;top:313px;display:flex;gap:4px;align-items:center}
.swatch{width:14px;height:14px}
.swatches .info{position:static;margin-left:8px}
.q-label{position:absolute;font-size:11px;font-weight:400;color:var(--ink-dark)}
.q-box{position:absolute;width:423px;height:133px;border:1px solid var(--line)}
.q-box .info{top:12px}
.save{position:absolute;left:485px;top:2458px;width:230px;height:54px;background:var(--pink);color:var(--white);font-size:16px;font-weight:500;line-height:54px;text-align:center;letter-spacing:.5px}
.footer{position:absolute;left:0;top:2587px;width:1200px;height:116px;background:var(--bar)}
.footer .brand{left:131px;top:47px}
.copyright{position:absolute;left:856px;top:53px;font-size:10px;color:#cfcfcf}
</style>
</head>
<body>
<svg width="0" height="0" style="position:absolute">
  <defs>
    <symbol id="i-info" viewBox="0 0 14 14">
      <circle cx="7" cy="7" r="7" fill="#b8b8b8"/>
      <rect x="6.1" y="6" width="1.8" height="4.8" fill="#fff"/>
      <rect x="6.1" y="3.2" width="1.8" height="1.8" fill="#fff"/>
    </symbol>
  </defs>
</svg>

<header class="topbar">
  <div class="brand">BLOOMWISE</div>
  <nav class="mainnav">
    <a href="#" style="left:328px">Plan</a>
    <a href="#" style="left:387px">Learn</a>
    <a href="#" style="left:452px">Remember</a>
  </nav>
  <nav class="usernav">
    <a href="#" style="left:948px">My Profile</a>
    <a href="#" style="left:1029px">Logout</a>
  </nav>
</header>

<nav class="subbar">
  <a href="#" class="active" style="left:121px">Your Business</a>
  <a href="#" style="left:259px">Your Products</a>
  <a href="#" style="left:389px">Your Customers</a>
  <a href="#" style="left:526px">Your Goals</a>
  <a href="#" style="left:631px">Your Plan</a>
</nav>

<section class="hero">
  <div class="profile-card">
    <div class="profile-mark"></div>
    <h1 class="profile-name">Clara Vance Beauty</h1>
    <div class="profile-email">info@claravancebeauty.com</div>
    <div class="profile-bio">
      <p>There are many variations of passages of Lorem Ipsum available, but the majority have suffered alteration in some form, by injected humour, or randomised words which don't look even slightly believable. If you are going to use a passage of Lorem Ipsum, you need to be sure there isn't anything embarrassing hidden in the middle of text.</p>
      <p>There are many variations of passages of Lorem Ipsum available, but the majority have suffered alteration in some form, by injected humour, or randomised words which don't look even slightly believable.</p>
    </div>
    <div class="profile-photo" role="img" aria-label="Portrait photo of a makeup artist applying eyeshadow"></div>
  </div>
</section>

<h2 class="section-title" style="top:576px">WHO YOU ARE</h2>
<section class="panel" style="top:623px;height:714px">
  <div class="field short with-upload" style="left:33px;top:26px"><span class="label">Logo</span><svg class="info"><use href="#i-info"/></svg><div class="upload"><svg width="9" height="10" viewBox="0 0 9 10"><path d="M4.5 0L8 4H5.6v3H3.4V4H1z M0 8.6h9V10H0z" fill="#2f5f59"/></svg>UPLOAD</div></div>
  <div class="field short" style="left:467px;top:26px"><span class="label">Business Name</span><svg class="info"><use href="#i-info"/></svg></div>
  <div class="field short" style="left:33px;top:82px"><span class="label">Business tag line</span><svg class="info"><use href="#i-info"/></svg></div>
  <div class="field short" style="left:467px;top:82px"><span class="label">Business vision</span><svg class="info"><use href="#i-info"/></svg></div>
  <div class="field tall" style="left:33px;top:138px"><span class="label">Business Bio</span><svg class="info"><use href="#i-info"/></svg></div>
  <div class="field tall" style="left:467px;top:138px"><span class="label">Key competitors</span><svg class="info"><use href="#i-info"/></svg></div>

  <div class="small-label" style="top:310px">Brand colours</div>
  <div class="swatches">
    <span class="swatch" style="background:#1e7fe0"></span>
    <span class="swatch" style="background:#2fa36f"></span>
    <span class="swatch" style="background:#9b8a2a"></span>
    <span class="swatch" style="background:#a61e22"></span>
    <span class="swatch" style="background:#2c7c8c"></span>
    <span class="swatch" style="background:#2cc4c4"></span>
    <svg class="info" width="14" height="14"><use href="#i-info"/></svg>
  </div>

  <div class="small-label" style="top:366px">SWOT analysis</div>
  <div class="field tall" style="left:33px;top:396px"><span class="label">Strengths</span><svg class="info"><use href="#i-info"/></svg></div>
  <div class="field tall" style="left:467px;top:396px"><span class="label">Weaknesses</span><svg class="info"><use href="#i-info"/></svg></div>
  <div class="field tall" style="left:33px;top:542px"><span class="label">Opportunities</span><svg class="info"><use href="#i-info"/></svg></div>
  <div class="field tall" style="left:467px;top:542px"><span class="label">Threats</span><svg class="info"><use href="#i-info"/></svg></div>
</section>

<h2 class="section-title" style="top:1389px">WHY YOU EXIST</h2>
<section class="panel" style="top:1436px;height:969px">
  <div class="q-label" style="left:33px;top:34px">Who are your ideal customers?</div>
  <div class="q-label" style="left:467px;top:34px">What problem are you trying to solve for them?</div>
  <div class="q-box" style="left:33px;top:58px"><svg class="info"><use href="#i-info"/></svg></div>
  <div class="q-box" style="left:467px;top:58px"><svg class="info"><use href="#i-info"/></svg></div>

  <div class="q-label" style="left:33px;top:216px">What pain points will this remove for them?</div>
  <div class="q-label" style="left:467px;top:216px">How do you solve it?</div>
  <div class="q-box" style="left:33px;top:240px"><svg class="info"><use href="#i-info"/></svg></div>
  <div class="q-box" style="left:467px;top:240px"><svg class="info"><use href="#i-info"/></svg></div>

  <div class="q-label" style="left:33px;top:400px">How else could this problem be solved?</div>
  <div class="q-label" style="left:467px;top:400px">Who offers these other solutions?</div>
  <div class="q-box" style="left:33px;top:423px"><svg class="info"><use href="#i-info"/></svg></div>
  <div class="q-box" style="left:467px;top:423px"><svg class="info"><use href="#i-info"/></svg></div>

  <div class="q-label" style="left:33px;top:586px">Why is your solution better?</div>
  <div class="q-label" style="left:467px;top:586px">How much does your solution cost?</div>
  <div class="q-box" style="left:33px;top:610px"><svg class="info"><use href="#i-info"/></svg></div>
  <div class="q-box" style="left:467px;top:610px"><svg class="info"><use href="#i-info"/></svg></div>

  <div class="q-label" style="left:33px;top:774px">What value are you providing to justify this cost?</div>
  <div class="q-label" style="left:467px;top:774px">How will this make their life/job easier/better?</div>
  <div class="q-box" style="left:33px;top:798px"><svg class="info"><use href="#i-info"/></svg></div>
  <div class="q-box" style="left:467px;top:798px"><svg class="info"><use href="#i-info"/></svg></div>
</section>

<div class="save">SAVE CHANGES</div>

<footer class="footer">
  <div class="brand">BLOOMWISE</div>
  <div class="copyright">Copyrights @ 2017 All Rights Reserved</div>
</footer>
</body>
</html>
```